Home Remodeling company needs a business card design

we need a business card design for home remodeling company in hamilton county, indiana USA. we offers a wide range of construction services including whole house renovations, Design and Build Basements and Kitchen and Bathroom Remodeling . we would like to see designs for both site of business card that use the same color of the company logo and also including all information below :
1- Karim Feltous CEO / General Contractor
2- all company contacts Telephone numbers ( 1-888-DULOM-47 ) ( 317-555-0193) email address ( info@dulomhome.com) website ( www.dulomhome.com ) and social media logos (Facebook- twitter- google plus )
3- company logo
4- licensed . insured . bonded

```html
<!DOCTYPE html>
<html lang="en">
<head>
<meta charset="UTF-8">
<title>Dulom Home Remodeling – Business Card</title>
<link href="https://fonts.googleapis.com/css2?family=Open+Sans:wght@400;600;700&display=swap" rel="stylesheet">
<style>
  :root {
    --backdrop: #2b2623;
    --card: #1c1c1d;
    --card-edge: #111112;
    --accent-red: #c8303a;
    --strip-grey: #3a3a3c;
    --text-light: #e6e6e6;
    --text-muted: #8d8d90;
    --logo-grey: #9a9a9d;
    --logo-silver: #d4d6da;
    --icon-grey: #6d6d71;
  }
  * { margin: 0; padding: 0; box-sizing: border-box; }
  html, body {
    width: 1200px; height: 780px; overflow: hidden;
    background: var(--backdrop);
    font-family: "Open Sans", sans-serif;
  }
  .canvas { position: relative; width: 1200px; height: 780px; }

  .card {
    position: absolute; top: 235px;
    width: 540px; height: 310px;
    background: var(--card);
    border: 1px solid var(--card-edge);
    overflow: hidden;
  }
  .card--front { left: 40px; }
  .card--back { left: 620px; }

  /* Front */
  .brand { position: absolute; left: 38px; top: 52px; width: 200px; }
  .brand__name {
    display: flex; align-items: center; gap: 10px;
    font-size: 44px; font-weight: 700; letter-spacing: 1px;
    color: var(--logo-grey); line-height: 1;
  }
  .brand__mark { width: 10px; height: 10px; background: var(--accent-red); }
  .brand__tagline {
    margin-top: 6px; font-size: 11px; letter-spacing: 5px;
    color: var(--logo-grey); text-transform: uppercase;
  }
  .brand__credentials {
    margin-top: 4px; font-size: 11px; color: var(--text-muted);
  }
  .social { position: absolute; left: 16px; top: 88px; display: flex; flex-direction: column; gap: 4px; }
  .social__icon { width: 9px; height: 9px; background: var(--icon-grey); }

  .divider {
    position: absolute; left: 262px; top: 40px;
    width: 1px; height: 160px; background: var(--accent-red);
  }

  .person { position: absolute; left: 280px; top: 44px; }
  .person__name { font-size: 22px; color: var(--accent-red); line-height: 1.1; }
  .person__role { font-size: 14px; color: var(--text-light); line-height: 1.25; }

  .contacts { position: absolute; left: 280px; top: 118px; list-style: none; }
  .contacts__item {
    display: flex; align-items: center; gap: 10px;
    font-size: 13px; color: var(--text-light); line-height: 21px;
  }
  .contacts__icon { width: 9px; height: 9px; flex: none; }

  .band-grey { position: absolute; left: 0; top: 214px; width: 100%; height: 8px; background: var(--strip-grey); }
  .band-red { position: absolute; left: 0; top: 222px; width: 100%; height: 30px; background: var(--accent-red); }

  /* Back */
  .back-brand {
    position: absolute; left: 0; right: 0; top: 108px; text-align: center;
  }
  .back-brand__name {
    display: inline-flex; align-items: center; gap: 14px;
    font-size: 66px; font-weight: 700; letter-spacing: 2px;
    color: var(--logo-silver); line-height: 1;
  }
  .back-brand__mark { width: 12px; height: 12px; background: var(--logo-silver); }
  .back-brand__tagline {
    margin-top: 8px; font-size: 15px; letter-spacing: 9px;
    color: var(--logo-silver); text-transform: uppercase;
  }
</style>
</head>
<body>
<main class="canvas">

  <section class="card card--front" aria-label="Business card front">
    <div class="social" aria-label="Social media">
      <span class="social__icon"></span>
      <span class="social__icon"></span>
      <span class="social__icon"></span>
    </div>
    <div class="brand">
      <div class="brand__name"><span class="brand__mark"></span>DULOM</div>
      <div class="brand__tagline">Home Remodeling</div>
      <div class="brand__credentials">licensed . insured . bonded</div>
    </div>

    <div class="divider"></div>

    <div class="person">
      <div class="person__name">Karim Feltous</div>
      <div class="person__role">General Contractor</div>
      <div class="person__role">CEO</div>
    </div>

    <ul class="contacts">
      <li class="contacts__item">
        <svg class="contacts__icon" viewBox="0 0 10 10"><rect width="10" height="10" fill="#c8303a"/><path d="M3 2.2 L4.2 2.2 L4.6 3.8 L3.9 4.4 Q4.6 5.8 5.8 6.3 L6.4 5.6 L8 6 L8 7.4 Q4.2 7.6 2.6 3.4 Z" fill="#1c1c1d"/></svg>
        1-888-DULOM-47
      </li>
      <li class="contacts__item">
        <svg class="contacts__icon" viewBox="0 0 10 10"><rect width="10" height="10" fill="#c8303a"/><rect x="3" y="2" width="4" height="6" rx="0.6" fill="#1c1c1d"/></svg>
        317-555-0193
      </li>
      <li class="contacts__item">
        <svg class="contacts__icon" viewBox="0 0 10 10"><rect width="10" height="10" fill="#c8303a"/><rect x="2" y="3" width="6" height="4" fill="#1c1c1d"/><path d="M2 3 L5 5.2 L8 3" stroke="#c8303a" stroke-width="0.7" fill="none"/></svg>
        info@dulomhome.com
      </li>
      <li class="contacts__item">
        <svg class="contacts__icon" viewBox="0 0 10 10"><rect width="10" height="10" fill="#c8303a"/><circle cx="5" cy="5" r="2.8" fill="none" stroke="#1c1c1d" stroke-width="0.8"/><path d="M2.2 5 H7.8 M5 2.2 V7.8" stroke="#1c1c1d" stroke-width="0.6"/></svg>
        www.dulomhome.com
      </li>
    </ul>

    <div class="band-grey"></div>
    <div class="band-red"></div>
  </section>

  <section class="card card--back" aria-label="Business card back">
    <div class="back-brand">
      <div class="back-brand__name"><span class="back-brand__mark"></span>DULOM</div>
      <div class="back-brand__tagline">Home Remodeling</div>
    </div>
  </section>

</main>
</body>
</html>
```